Stretch on the Green with Mira

I want to advertise my Stretch on the Green classes for Summer. Classes are outside at the lovely local park. Tolmore field. 12 Rawhiti St. Sandringham.
Classes are for beginners to advance levels.
Classes start Monday, October 17th.
Monday 6pm Beginners
Tuesday 6pm Intermediate
Thursday 6pm Intermediate/Advance
Saturday 9am All fitness levels
My Pilates classes are specially designed to help improve strength and flexibility but as well will also improve posture, reduce stress and develop control and endurance in the entire body.
Booking essential. Limited numbers so I can make sure the correct technique is always being followed.
For more info or to book contact details:
Mira 027385116
mira@stretchwithmira.net
www.stretchwithmira.net
$15 Per Session

Target Market(s)

Males and Females ages 35plus.

Industry/Entity Type

Fitness

Font styles to use
Sans Serif

Requirements
Must have
• My logo. Contact details. A Park that looks lovely to exercise at.
Nice to have
• Summer looking. Trees - inspiration to be exercising outside

```html
<!DOCTYPE html>
<html lang="en">
<head>
<meta charset="utf-8">
<title>Stretch on the Green with Mira – Summer Classes</title>
<link href="https://fonts.googleapis.com/css2?family=Poppins:wght@400;500;600;700;800&family=Great+Vibes&display=swap" rel="stylesheet">
<style>
:root{
  --pink:#ee6db6;
  --pink-soft:#f49ccc;
  --charcoal:#474747;
  --green:#0e6b55;
  --red:#e5252a;
  --cream:#fbeee5;
  --white:#ffffff;
  --stage:#ebebeb;
}
*{box-sizing:border-box;margin:0;padding:0}
html,body{width:1200px;height:3200px;overflow:hidden}
body{background:var(--stage);font-family:'Poppins',sans-serif;color:var(--charcoal)}
.flyer{position:absolute;left:0;top:750px;width:1200px;height:1700px;background:var(--white);overflow:hidden;box-shadow:0 10px 30px rgba(0,0,0,.15)}
.hero{position:absolute;left:0;top:0;width:1200px;height:820px}
.brand-arch{position:absolute;left:274px;top:0;width:626px;height:178px}
.brand{position:absolute;left:274px;top:60px;width:626px;display:flex;align-items:center;justify-content:center;gap:14px;color:var(--pink);font-size:28px;font-weight:500;letter-spacing:2px}
.brand-dot{width:22px;height:22px;border-radius:50%;background:var(--pink)}
.title{position:absolute;left:0;top:640px;width:1200px;text-align:center;font-weight:800;line-height:1;text-transform:uppercase;z-index:2}
.title-top{color:var(--pink);font-size:82px;letter-spacing:-1px}
.title-bottom{color:var(--charcoal);font-size:82px;letter-spacing:-1px;margin-top:-4px}
.title-script{font-family:'Great Vibes',cursive;text-transform:none;font-weight:400;font-size:90px;margin-left:10px}
.season-bar{position:absolute;left:269px;top:822px;width:660px;height:54px;background:var(--charcoal);color:var(--white);text-align:center;font-weight:700;font-size:40px;line-height:54px}
.season-bar span{color:var(--pink)}
.venue-line{position:absolute;left:0;top:882px;width:1200px;text-align:center;font-weight:700;font-size:33px}
.schedule{position:absolute;left:100px;top:955px;width:982px;height:310px;border:3px solid var(--pink);border-radius:14px;overflow:hidden;box-shadow:0 6px 10px rgba(0,0,0,.2);background:var(--white)}
.schedule-head{background:var(--pink);height:120px;position:relative}
.level-tab{position:absolute;left:140px;top:0;width:702px;height:44px;background:var(--green);color:var(--white);border-radius:0 0 14px 14px;text-align:center;font-size:25px;line-height:44px}
.level-tab b{font-weight:700}
.start-date{position:absolute;left:0;top:50px;width:100%;text-align:center;color:var(--white);font-weight:800;font-size:40px}
.start-date em{font-style:normal;color:var(--charcoal)}
.start-date sup{font-size:22px}
.binding{position:absolute;left:0;bottom:0;width:100%;height:22px}
.timetable{width:100%;border-collapse:collapse;table-layout:fixed;text-align:center}
.timetable th.row-label{width:106px;background:var(--green);color:var(--white);font-size:22px;font-weight:700;border-bottom:2px solid var(--white)}
.timetable td{border-left:2px solid #8a8a8a;border-bottom:2px solid #8a8a8a}
.day-row td{height:48px;color:var(--green);font-weight:700;font-size:21px}
.time-row td{height:54px;font-weight:600;font-size:30px}
.level-row td{height:80px;background:var(--pink);color:var(--white);font-weight:700;font-size:20px;line-height:1.05;border-color:var(--white)}
.price{position:absolute;left:293px;top:1290px;width:610px;height:76px;background:var(--red);border-radius:14px 14px 0 0;color:var(--white);text-align:center;font-weight:700;font-size:60px;line-height:80px;z-index:2;overflow:hidden}
.price sup{font-size:32px;vertical-align:20px;line-height:0}
.benefits{position:absolute;left:0;top:1366px;width:1200px;height:136px;background:var(--charcoal);color:var(--white)}
.benefits h2{text-align:center;font-size:29px;font-weight:700;margin-top:8px}
.benefit-list{display:flex;justify-content:center;margin-top:12px;list-style:none}
.benefit{display:flex;align-items:center;gap:12px;padding:0 16px;font-size:21px;line-height:1.15;border-right:2px solid #6b6b6b}
.benefit:last-child{border-right:none}
.benefit-icon{width:46px;height:46px;border-radius:50%;background:var(--white);border:2px solid #d9d9d9;flex:none}
.booking{position:absolute;left:72px;top:1518px;width:1050px;height:60px;display:flex;border:2px solid var(--pink-soft)}
.booking-label{width:172px;background:var(--pink);color:var(--white);font-weight:700;font-size:22px;line-height:1.05;display:flex;align-items:center;padding-left:20px}
.booking-note{flex:1;background:var(--cream);display:flex;align-items:center;padding-left:14px;font-size:19px}
.contact{position:absolute;left:0;top:1600px;width:1200px;height:100px}
.contact-name{position:absolute;left:0;top:0;width:310px;height:100px;background:var(--green);clip-path:polygon(0 0,270px 0,310px 100%,0 100%);color:var(--white);font-weight:700;font-size:50px;line-height:100px;padding-left:70px}
.contact-head{position:absolute;left:290px;top:0;width:910px;height:38px;background:var(--charcoal);color:var(--white);text-align:center;font-size:21px;line-height:38px}
.contact-row{position:absolute;left:300px;top:38px;width:900px;height:62px;background:var(--cream);display:flex;align-items:center;gap:22px;padding-left:20px;font-weight:600;font-size:21px;color:#222}
.contact-row .phone{font-size:25px}
.contact-item{display:flex;align-items:center;gap:8px}
.contact-item svg{flex:none}
</style>
</head>
<body>
<main class="flyer">
  <svg class="hero" viewBox="0 0 1200 820" role="img" aria-label="Photo of adults stretching on yoga mats on the grass of a sunny, tree-lined park">
    <defs>
      <linearGradient id="parkTone" x1="0" y1="0" x2="0" y2="1">
        <stop offset="0" stop-color="#5f7d3a"/>
        <stop offset="0.45" stop-color="#3f6a2c"/>
        <stop offset="1" stop-color="#74a83f"/>
      </linearGradient>
      <radialGradient id="sunGlow" cx="0.2" cy="0.15" r="0.5">
        <stop offset="0" stop-color="#e8d88a" stop-opacity=".7"/>
        <stop offset="1" stop-color="#e8d88a" stop-opacity="0"/>
      </radialGradient>
    </defs>
    <rect width="1200" height="820" fill="url(#parkTone)"/>
    <rect width="1200" height="820" fill="url(#sunGlow)"/>
    <path d="M0,752 C300,622 760,578 1200,692 L1200,820 L0,820 Z" fill="#ffffff"/>
    <path d="M0,700 C260,608 560,586 780,594 C540,604 260,662 0,746 Z" fill="#ee6db6"/>
    <path d="M640,586 C900,588 1100,636 1200,672 L1200,698 C1080,656 880,598 640,594 Z" fill="#474747"/>
  </svg>

  <svg class="brand-arch" viewBox="0 0 626 178" aria-hidden="true">
    <path d="M0,0 L626,0 C590,120 470,178 300,178 C150,178 40,120 0,0 Z" fill="#474747"/>
    <path d="M595,0 C560,120 440,182 300,182" fill="none" stroke="#ffffff" stroke-width="5"/>
  </svg>
  <div class="brand"><span class="brand-dot"></span>STRETCH WITH MIRA</div>

  <h1 class="title">
    <div class="title-top">Stretch on</div>
    <div class="title-bottom">the Green<span class="title-script">with Mira</span></div>
  </h1>

  <div class="season-bar"><span>CLASSES FOR</span> SUMMER</div>
  <p class="venue-line">CLASSES ARE OUTSIDE AT THE LOVELY LOCAL PARK</p>

  <section class="schedule">
    <div class="schedule-head">
      <div class="level-tab">CLASSES ARE FOR <b>BEGINNERS TO ADVANCE LEVELS</b></div>
      <div class="start-date">CLASSES START MONDAY, <em>OCTOBER 17<sup>TH</sup></em></div>
      <svg class="binding" viewBox="0 0 982 22" preserveAspectRatio="none" aria-hidden="true">
        <defs>
          <pattern id="coil" width="12" height="22" patternUnits="userSpaceOnUse">
            <rect x="4" y="4" width="4" height="14" rx="2" fill="#ffffff" stroke="#555" stroke-width="1"/>
          </pattern>
        </defs>
        <rect width="982" height="22" fill="url(#coil)"/>
      </svg>
    </div>
    <table class="timetable">
      <tr class="day-row"><th class="row-label">DAY</th><td>MONDAY</td><td>TUESDAY</td><td>THURSDAY</td><td>SATURDAY</td></tr>
      <tr class="time-row"><th class="row-label">TIME</th><td>6 PM</td><td>6 PM</td><td>6 PM</td><td>9 AM</td></tr>
      <tr class="level-row"><th class="row-label">LEVELS</th><td>BEGINNERS</td><td>INTERMEDIATE</td><td>INTERMEDIATE/<br>ADVANCE</td><td>ALL FITNESS<br>LEVELS</td></tr>
    </table>
  </section>

  <div class="price"><sup>$</sup>15 PER SESSION</div>

  <section class="benefits">
    <h2>MY PILATES CLASSES ARE SPECIALLY DESIGNED TO HELP</h2>
    <ul class="benefit-list">
      <li class="benefit"><span class="benefit-icon"></span>Improve strength<br>and flexibility</li>
      <li class="benefit"><span class="benefit-icon"></span>Improve<br>posture</li>
      <li class="benefit"><span class="benefit-icon"></span>Reduce<br>stress</li>
      <li class="benefit"><span class="benefit-icon"></span>Develop<br>control</li>
      <li class="benefit"><span class="benefit-icon"></span>Endurance in<br>the entire body</li>
    </ul>
  </section>

  <div class="booking">
    <div class="booking-label">BOOKING<br>ESSENTIAL</div>
    <div class="booking-note">Limited numbers so I can make sure the correct technique is always being followed.</div>
  </div>

  <footer class="contact">
    <div class="contact-name">MIRA</div>
    <div class="contact-head">FOR MORE INFO OR TO BOOK CONTACT DETAILS:</div>
    <div class="contact-row">
      <span class="contact-item phone">
        <svg width="24" height="24" viewBox="0 0 24 24" aria-hidden="true"><path d="M6.6 10.8a15 15 0 0 0 6.6 6.6l2.2-2.2c.3-.3.7-.4 1-.2 1.1.4 2.3.6 3.6.6.6 0 1 .4 1 1V20c0 .6-.4 1-1 1A17 17 0 0 1 3 4c0-.6.4-1 1-1h3.5c.6 0 1 .4 1 1 0 1.3.2 2.5.6 3.6.1.3 0 .7-.2 1z" fill="#0e6b55"/></svg>
        027385116
      </span>
      <span class="contact-item">
        <svg width="20" height="20" viewBox="0 0 24 24" aria-hidden="true"><rect x="2" y="5" width="20" height="14" rx="2" fill="#0e6b55"/><path d="M2 6l10 7 10-7" fill="none" stroke="#fbeee5" stroke-width="2"/></svg>
        mira@stretchwithmira.net
      </span>
      <span class="contact-item">
        <svg width="20" height="20" viewBox="0 0 24 24" aria-hidden="true"><circle cx="12" cy="12" r="10" fill="none" stroke="#0e6b55" stroke-width="2"/><path d="M2 12h20M12 2c3 3 3 17 0 20M12 2c-3 3-3 17 0 20" fill="none" stroke="#0e6b55" stroke-width="1.6"/></svg>
        www.stretchwithmira.net
      </span>
    </div>
  </footer>
</main>
</body>
</html>
```